Banner Pop Up Opt In Form REDESIGNS - SLEEK BLACK LOOK

Please redesign banners attached.

I am looking for a very sleek look....I do not like this collage of images on these current designs. Please keep all content same but use images that pop.

I have an acccount at www.pixvane-example.com or you can use your own images.

I like black background for somereason because it looks very sleek....but these designs should pop , build trust and credibility and have easy opt in form....SLEEK AND MODERN LOOK is what im looking for....

Target Market(s)

Consumers on websites

Requirements
Must have
• Please redesign banners attached.

Nice to have

Should not have

```html
<!DOCTYPE html>
<html lang="en">
<head>
<meta charset="UTF-8">
<title>Free Sample Opt-In Banner</title>
<link href="https://fonts.googleapis.com/css2?family=Arimo:wght@400;700&family=Poppins:wght@300;400&display=swap" rel="stylesheet">
<style>
  :root {
    --bg-black: #000000;
    --panel-shade: rgba(0, 0, 0, 0.72);
    --headline-green: #1fe85f;
    --accent-yellow: #f7b500;
    --text-white: #ffffff;
    --field-white: #ffffff;
    --field-border: #8aa0c8;
    --field-text: #111111;
    --button-blue: #0a3cf0;
    --photo-deep: #0a0f12;
    --photo-mid: #2d4652;
    --photo-light: #4f6f7c;
  }
  * { margin: 0; padding: 0; box-sizing: border-box; }
  html, body {
    width: 1200px;
    height: 1032px;
    overflow: hidden;
    background: var(--bg-black);
  }
  .banner {
    position: relative;
    width: 1200px;
    height: 1032px;
    overflow: hidden;
    background: var(--bg-black);
    font-family: "Arimo", Arial, sans-serif;
  }
  .banner__photo {
    position: absolute;
    inset: 0;
    background:
      radial-gradient(ellipse 420px 520px at 860px 300px, var(--photo-light) 0%, var(--photo-mid) 45%, transparent 80%),
      radial-gradient(ellipse 500px 380px at 880px 640px, #1f2f37 0%, transparent 75%),
      linear-gradient(90deg, var(--photo-deep) 0%, #111a1f 40%, #1a2a31 70%, var(--photo-deep) 100%);
  }
  .banner__shade {
    position: absolute;
    left: 0;
    top: 0;
    width: 578px;
    height: 1032px;
    background: var(--panel-shade);
  }
  .banner__content {
    position: absolute;
    left: 33px;
    top: 0;
    width: 520px;
  }
  .headline {
    position: absolute;
    top: 34px;
    left: 0;
    font-weight: 700;
    font-size: 48px;
    line-height: 56px;
    color: var(--headline-green);
    white-space: nowrap;
  }
  .subline {
    position: absolute;
    top: 164px;
    left: 0;
    font-weight: 700;
    font-size: 24px;
    line-height: 29px;
    color: var(--text-white);
    white-space: nowrap;
  }
  .product-name {
    position: absolute;
    top: 248px;
    left: 0;
    font-weight: 700;
    font-size: 24px;
    line-height: 29px;
    color: var(--accent-yellow);
    white-space: nowrap;
  }
  .optin-form {
    position: absolute;
    top: 350px;
    left: 0;
    width: 437px;
  }
  .optin-form__field {
    display: block;
    width: 437px;
    height: 62px;
    margin-bottom: 7px;
    padding: 0 20px;
    background: var(--field-white);
    border: 1px solid var(--field-border);
    border-radius: 7px;
    font-family: "Poppins", Arial, sans-serif;
    font-size: 25px;
    color: var(--field-text);
    outline: none;
  }
  .optin-form__field::placeholder { color: var(--field-text); opacity: 1; }
  .optin-form__submit {
    display: block;
    width: 437px;
    height: 75px;
    margin-top: 0;
    border: none;
    border-radius: 7px;
    background: var(--button-blue);
    color: var(--text-white);
    font-family: "Poppins", Arial, sans-serif;
    font-weight: 300;
    font-size: 33px;
    letter-spacing: 0.5px;
  }
  .delivery-note {
    position: absolute;
    top: 953px;
    left: 0;
    font-size: 24px;
    line-height: 29px;
    color: var(--text-white);
  }
</style>
</head>
<body>
  <section class="banner">
    <div class="banner__photo" role="img" aria-label="Person in a teal training shirt fastening a black smart fitness watch on their wrist against a dark background"></div>
    <div class="banner__shade"></div>
    <div class="banner__content">
      <h1 class="headline">GET A<br>FREE SAMPLE</h1>
      <p class="subline">ENTER YOUR DETAILS BELOW TO<br>GET YOUR FREE SAMPLE</p>
      <p class="product-name">SMART FITNESS WATCH</p>
      <form class="optin-form">
        <input class="optin-form__field" type="text" placeholder="Name">
        <input class="optin-form__field" type="email" placeholder="Email">
        <input class="optin-form__field" type="tel" placeholder="Phone">
        <button class="optin-form__submit" type="button">SUBMIT</button>
      </form>
      <p class="delivery-note">Receive a sample by email, text message<br>and an instant pdf download.</p>
    </div>
  </section>
</body>
</html>
```